Veldmark Supplies Business Card

Professional business card that stand out to our potential customers. Front and back with clean modern design

Industry/Entity Type

Oil and gas

Contact Information for Business Card

Name, address, website , office phone and cell number

Requirements
Must have
• Editable files for each employee

```html
<!DOCTYPE html>
<html lang="en">
<head>
<meta charset="utf-8">
<title>Veldmark Supplies Business Card</title>
<link href="https://fonts.googleapis.com/css2?family=Montserrat:wght@400;500;700;800&display=swap" rel="stylesheet">
<style>
  :root {
    --brand-red: #ff0000;
    --brand-cyan: #05b1d6;
    --paper: #ffffff;
    --backdrop: #e9e6e2;
    --ink-light: #ffffff;
  }
  * { box-sizing: border-box; margin: 0; padding: 0; }
  html, body { width: 1200px; height: 878px; overflow: hidden; }
  body {
    background: var(--backdrop);
    font-family: "Montserrat", Arial, sans-serif;
    position: relative;
  }
  .card {
    position: absolute;
    top: 54px;
    width: 440px;
    height: 770px;
    border-radius: 32px;
    overflow: hidden;
    box-shadow: 0 10px 26px rgba(0,0,0,.22);
  }
  /* Front */
  .card-front { left: 90px; background: var(--brand-red); }
  .front-mark {
    position: absolute; left: 0; right: 0; top: 330px;
    display: flex; flex-direction: column; align-items: center; gap: 22px;
  }
  .mark-square { width: 70px; height: 70px; background: var(--ink-light); }
  .wordmark {
    color: var(--ink-light); font-weight: 800; font-size: 34px;
    letter-spacing: 2px; text-transform: uppercase; text-align: center; line-height: 1.15;
  }
  /* Back */
  .card-back { left: 670px; background: var(--brand-cyan); }
  .back-top {
    position: absolute; inset: 0;
    background: var(--paper);
    clip-path: polygon(0 0, 100% 0, 100% 26%, 0 48%);
  }
  .back-header {
    position: absolute; top: 34px; left: 0; right: 0; text-align: center;
    color: var(--brand-red); font-weight: 800; font-size: 22px; letter-spacing: 2px;
    text-transform: uppercase;
  }
  .back-mark {
    position: absolute; top: 150px; left: 0; right: 0;
    display: flex; flex-direction: column; align-items: center; gap: 14px;
  }
  .back-mark .mark-square { background: var(--brand-red); width: 60px; height: 60px; }
  .back-mark .wordmark { color: var(--brand-red); font-size: 28px; }
  .person { position: absolute; top: 400px; left: 0; right: 0; text-align: center; color: var(--ink-light); }
  .person-name { font-weight: 700; font-size: 28px; letter-spacing: 1px; text-transform: uppercase; }
  .person-title {
    display: flex; align-items: center; justify-content: center; gap: 12px;
    font-size: 16px; font-weight: 500; margin-top: 2px;
  }
  .person-title::before, .person-title::after {
    content: ""; width: 90px; height: 2px; background: var(--ink-light);
  }
  .icon-row { position: absolute; top: 490px; left: 0; right: 0; display: flex; justify-content: center; gap: 18px; }
  .icon-box {
    width: 38px; height: 38px; background: var(--brand-red);
    display: flex; align-items: center; justify-content: center;
  }
  .contact {
    position: absolute; top: 548px; left: 0; right: 0; text-align: center;
    color: var(--ink-light); font-size: 17px; line-height: 1.45; font-weight: 500;
  }
  .rule { position: absolute; left: 70px; right: 70px; height: 2px; background: var(--ink-light); }
  .address {
    position: absolute; top: 680px; left: 0; right: 0; text-align: center;
    color: var(--ink-light); font-size: 17px; line-height: 1.4; font-weight: 500;
  }
</style>
</head>
<body>
  <section class="card card-front" aria-label="Card front">
    <div class="front-mark">
      <div class="mark-square"></div>
      <div class="wordmark">Veldmark<br>Supplies</div>
    </div>
  </section>

  <section class="card card-back" aria-label="Card back">
    <div class="back-top"></div>
    <div class="back-header">Veldmark Supplies</div>
    <div class="back-mark">
      <div class="mark-square"></div>
      <div class="wordmark">Veldmark Supplies</div>
    </div>
    <div class="person">
      <div class="person-name">Dalen Hartwick</div>
      <div class="person-title">President</div>
    </div>
    <div class="icon-row">
      <div class="icon-box"><svg width="22" height="22" viewBox="0 0 24 24" fill="#fff"><path d="M6.6 10.8a15 15 0 0 0 6.6 6.6l2.2-2.2c.3-.3.7-.4 1-.2 1.1.4 2.3.6 3.6.6.6 0 1 .4 1 1V20c0 .6-.4 1-1 1A17 17 0 0 1 3 4c0-.6.4-1 1-1h3.5c.6 0 1 .4 1 1 0 1.3.2 2.5.6 3.6.1.3 0 .7-.2 1z"/></svg></div>
      <div class="icon-box"><svg width="22" height="22" viewBox="0 0 24 24" fill="none" stroke="#fff" stroke-width="2"><rect x="7" y="2" width="10" height="20" rx="2"/><line x1="11" y1="18" x2="13" y2="18"/></svg></div>
      <div class="icon-box"><svg width="22" height="22" viewBox="0 0 24 24" fill="none" stroke="#fff" stroke-width="2"><rect x="3" y="5" width="18" height="14"/><polyline points="3,5 12,13 21,5"/></svg></div>
      <div class="icon-box"><svg width="22" height="22" viewBox="0 0 24 24" fill="none" stroke="#fff" stroke-width="2"><circle cx="12" cy="12" r="9"/><ellipse cx="12" cy="12" rx="4" ry="9"/><line x1="3" y1="12" x2="21" y2="12"/></svg></div>
    </div>
    <div class="contact">
      555-210-4476<br>
      000-000-9999<br>
      info@example-youremail.com<br>
      www.example-yourwebsite.com
    </div>
    <div class="rule" style="top:668px"></div>
    <div class="address">482 Orrin Ave, Ste<br>100, Halden, TX 75201</div>
  </section>
</body>
</html>
```